Real Estate Company Looking for Business Card Designs for 3 Executives

Hello!
Thanks so much for considering our project! We are a real estate investment company located in Edmonton, Alberta called Bellhaven Group of Companies. We invest/develop both commercial and residential real estate and are looking to create 3 DOUBLE-SIDED business cards for 3 top executives in the company! (for some reason it won't let us select the double-sided option, but yes, the cards are double sided and would be happy to tip extra)

We have certain guidelines that we want our business cards to for sure follow - the back of the Business card has to be the Black Background Version of the Logo which has already been designed and linked as a file (first file). We want the entire back of the card to simply just be the black background logo. In terms of the front of the card, would like to see a smaller version of the white background logo (linked as the second file) in the top left hand corner - of course, feel free to get creative and we can make revisions together along the way! and Then after that, just text. We want the card to be sharp, clean, easy on the eyes and highly professional looking. We would like the card to include the Full name of the Company (Bellhaven Group of Companies), Name of the Person, Title, Phone, Email. If possible please provide the front part of the card for 3 people:

1) Bellhaven Group of Companies, Liora Quenby, Chief Financial Officer, 780-555-0142, lioraquenby@bellhavengroup.example

2) Bellhaven Group of Companies, Tobias Quenby, Chief Executive Officer, 780-555-0187, tobiasquenby@bellhavengroup.example

3) Bellhaven Group of Companies, Rui Delcourt, Chief Operations Officer, 587-555-0163, ruidelcourt@bellhavengroup.example

Thank you so much for considering our project & we look forward to seeing your designs!

```html
<!DOCTYPE html>
<html lang="en">
<head>
<meta charset="utf-8">
<title>Bellhaven Group of Companies – Business Card</title>
<link rel="stylesheet" href="https://fonts.googleapis.com/css2?family=Arimo:wght@400&family=Jost:wght@400&family=Tinos:wght@700&display=swap">
<style>
  :root {
    --stage: #2a2a2a;
    --card-front: #ffffff;
    --card-back: #1e1e1e;
    --ink: #1d1d1d;
    --ink-soft: #262626;
    --ghost: #f2f2f2;
    --back-mark: #3c3c3c;
  }
  * { margin: 0; padding: 0; box-sizing: border-box; }
  html, body {
    width: 1200px; height: 1059px; overflow: hidden;
    background: var(--stage);
  }
  .canvas { position: relative; width: 1200px; height: 1059px; }

  .card { position: absolute; overflow: hidden; }
  .card--front {
    left: 256px; top: 89px; width: 688px; height: 391px;
    background: var(--card-front);
  }
  .card--back {
    left: 253px; top: 547px; width: 694px; height: 393px;
    background: var(--card-back);
  }

  .brand {
    position: absolute; left: 34px; top: 62px;
    display: flex; align-items: center; gap: 12px;
    font-family: "Jost", sans-serif; font-weight: 400;
    color: var(--ink);
  }
  .brand__square { width: 34px; height: 34px; background: var(--ink); flex: none; }
  .brand__name { font-size: 21px; letter-spacing: 3px; line-height: 1.25; text-transform: uppercase; }
  .brand__name span { display: block; font-size: 11px; letter-spacing: 2.6px; }

  .ghost-name {
    position: absolute; right: -8px; top: 120px;
    font-family: "Jost", sans-serif; font-weight: 400;
    font-size: 112px; letter-spacing: -2px; line-height: 1;
    color: var(--ghost);
  }

  .person {
    position: absolute; right: 29px; top: 173px; text-align: right;
  }
  .person__name {
    font-family: "Tinos", serif; font-weight: 700;
    font-size: 22px; letter-spacing: 0.6px; color: var(--ink);
    text-transform: uppercase;
  }
  .person__title {
    font-family: "Arimo", sans-serif; font-size: 16px; color: var(--ink-soft);
    margin-top: 1px;
  }

  .contact {
    position: absolute; left: 33px; top: 279px; list-style: none;
    font-family: "Arimo", sans-serif; font-size: 16px; color: var(--ink-soft);
  }
  .contact__item { display: flex; align-items: center; gap: 7px; height: 25px; }
  .contact__icon { width: 12px; height: 12px; flex: none; fill: var(--ink); }

  .back-mark {
    position: absolute; left: 0; right: 0; top: 150px; text-align: center;
    font-family: "Jost", sans-serif; font-weight: 400;
    font-size: 72px; letter-spacing: 8px; color: var(--back-mark);
    text-transform: uppercase;
  }
</style>
</head>
<body>
<main class="canvas">
  <section class="card card--front" aria-label="Card front">
    <div class="ghost-name" aria-hidden="true">Bellhaven</div>

    <div class="brand">
      <div class="brand__square" aria-hidden="true"></div>
      <div class="brand__name">Bellhaven<span>Group of Companies</span></div>
    </div>

    <div class="person">
      <h1 class="person__name">Tobias Quenby</h1>
      <p class="person__title">Chief Executive Officer</p>
    </div>

    <ul class="contact">
      <li class="contact__item">
        <svg class="contact__icon" viewBox="0 0 24 24" aria-hidden="true"><path d="M6.6 10.8a15.1 15.1 0 0 0 6.6 6.6l2.2-2.2a1 1 0 0 1 1-.25 11.4 11.4 0 0 0 3.6.57 1 1 0 0 1 1 1V20a1 1 0 0 1-1 1A17 17 0 0 1 3 4a1 1 0 0 1 1-1h3.5a1 1 0 0 1 1 1c0 1.25.2 2.45.57 3.57a1 1 0 0 1-.25 1z"/></svg>
        780-555-0187
      </li>
      <li class="contact__item">
        <svg class="contact__icon" viewBox="0 0 24 24" aria-hidden="true"><path d="M2 5h20v14H2z M2 5l10 8 10-8" fill="none" stroke="#1d1d1d" stroke-width="2.4"/><path d="M2 5h20L12 13z"/></svg>
        tobiasquenby@bellhavengroup.example
      </li>
      <li class="contact__item">
        <svg class="contact__icon" viewBox="0 0 24 24" aria-hidden="true"><circle cx="12" cy="12" r="10"/><path d="M7 6c2 1 2 3 4 3s1 3 3 3 2 2 0 4-1 3-1 4" fill="none" stroke="#fff" stroke-width="2"/></svg>
        www.bellhavengroup.example
      </li>
    </ul>
  </section>

  <section class="card card--back" aria-label="Card back">
    <div class="back-mark">Bellhaven</div>
  </section>
</main>
</body>
</html>
```